Business Card for Professional Photographer

I'm looking for an eye catching modern clean design that compliments my logo/ website fonts & colours.
I specialise in architecture, corporate & commercial photography so I'm marketing to professional clients rather than portrait / wedding clients.

I would prefer to not have a solid black design.

My logo brand guide is as follows :

Main front font. : Reislust
Main font colour : #fff
Slogan front font : Ubuntu Bold
Monogram front font : Venti Medium
Container colour : #fff

I need print ready files in pdf .png & .eps formats.

Included in the files below are some screen grabs as reference to font & colours etc.

```html
<!DOCTYPE html>
<html lang="en">
<head>
<meta charset="utf-8">
<title>Northlight Studio – Business Card</title>
<link rel="stylesheet" href="https://fonts.googleapis.com/css2?family=Ubuntu:wght@300;400;500;700&display=swap">
<style>
  :root {
    --backdrop: #39393c;
    --card-light: #4a4a4e;
    --card-mid: #36363a;
    --card-dark: #262628;
    --card-edge: #b27a3c;
    --gold: #d29a52;
    --ink: #f0f0f0;
    --emboss: #8e8e92;
    --rule: #dcdcdc;
  }
  * { box-sizing: border-box; margin: 0; padding: 0; }
  html, body {
    width: 1200px; height: 900px; overflow: hidden;
    background: var(--backdrop);
    font-family: "Ubuntu", sans-serif;
  }
  .canvas {
    width: 1200px; height: 900px;
    display: flex; flex-direction: column; align-items: center; justify-content: center;
    gap: 44px;
  }
  .card {
    position: relative;
    width: 680px; height: 388px;
    background:
      radial-gradient(ellipse at 20% 0%, rgba(255,255,255,.10), transparent 60%),
      linear-gradient(135deg, var(--card-light) 0%, var(--card-mid) 45%, var(--card-dark) 100%);
    border-bottom: 4px solid var(--card-edge);
    box-shadow: 0 10px 30px rgba(0,0,0,.45);
  }
  .brand { position: absolute; display: flex; align-items: center; gap: 18px; white-space: nowrap; }
  .brand-square { width: 30px; height: 30px; border: 2px solid currentColor; flex: none; }
  .brand-text { display: flex; flex-direction: column; gap: 4px; }
  .brand-name { font-weight: 300; font-size: 26px; letter-spacing: 4px; text-transform: uppercase; }
  .brand-tagline { font-weight: 700; font-size: 9px; letter-spacing: 2.6px; }

  .card-front .brand { left: 50%; top: 50%; transform: translate(-50%, -50%); color: var(--emboss); }

  .card-back .brand { right: 48px; top: 62px; color: var(--gold); }
  .card-back .brand-name { font-size: 24px; }

  .holder { position: absolute; left: 44px; top: 178px; }
  .holder-name { color: var(--gold); font-weight: 500; font-size: 25px; letter-spacing: .5px; }
  .holder-role { color: var(--ink); font-weight: 400; font-size: 18px; margin-top: 2px; }

  .divider { position: absolute; left: 40px; right: 40px; top: 254px; height: 1px; background: var(--rule); }

  .contacts { position: absolute; left: 44px; top: 270px; list-style: none; }
  .contacts li { display: flex; align-items: center; gap: 10px; color: var(--ink); font-size: 17px; line-height: 24px; white-space: nowrap; }
  .contacts svg { width: 13px; height: 13px; fill: var(--gold); flex: none; }

  .address { position: absolute; right: 44px; top: 272px; text-align: right; color: var(--ink); font-size: 18px; line-height: 24px; font-style: normal; white-space: nowrap; }
  .website { position: absolute; right: 44px; top: 334px; color: var(--gold); font-size: 17px; letter-spacing: 3px; white-space: nowrap; }
</style>
</head>
<body>
<main class="canvas">

  <section class="card card-front" aria-label="Card front">
    <div class="brand">
      <span class="brand-square"></span>
      <div class="brand-text">
        <span class="brand-name">Northlight Studio</span>
        <span class="brand-tagline">Architecture Corporate Commercial</span>
      </div>
    </div>
  </section>

  <section class="card card-back" aria-label="Card back">
    <div class="brand">
      <span class="brand-square"></span>
      <div class="brand-text">
        <span class="brand-name">Northlight Studio</span>
        <span class="brand-tagline">Architecture Corporate Commercial</span>
      </div>
    </div>

    <div class="holder">
      <p class="holder-name">Daniel Harper</p>
      <p class="holder-role">President</p>
    </div>

    <div class="divider"></div>

    <ul class="contacts">
      <li><svg viewBox="0 0 16 16" aria-hidden="true"><path d="M3.6 1l2.6 3-1.5 1.8c.9 2 2.5 3.6 4.5 4.5L11 8.8l3 2.6-1.4 2.8C7 14.2 1.8 9 1.8 3.4z"/></svg>555-240-1183</li>
      <li><svg viewBox="0 0 16 16" aria-hidden="true"><path d="M4 0h8a1 1 0 0 1 1 1v14a1 1 0 0 1-1 1H4a1 1 0 0 1-1-1V1a1 1 0 0 1 1-1zm1 2v10h6V2zm3 11a1 1 0 1 0 0 2 1 1 0 0 0 0-2z"/></svg>555-618-7720</li>
      <li><svg viewBox="0 0 16 16" aria-hidden="true"><path d="M4 1h6l2 2v3H4zM1 7h14v6h-3v2H4v-2H1zm4 4v3h6v-3z"/></svg>555-392-4406</li>
      <li><svg viewBox="0 0 16 16" aria-hidden="true"><path d="M0 3h16v10H0zm1.5 1.2L8 9l6.5-4.8V4H1.5z"/></svg>hello@northlightstudio.com</li>
    </ul>

    <address class="address">
      214 Willow Bend Road<br>Juneau, Alaska 99801
    </address>
    <p class="website">www.northlightstudio.com</p>
  </section>

</main>
</body>
</html>
```